Executive Taxi firm with Chauffeur service Website

I have my domain name registered and I have started to work on my site but I am struggling. I am just about to get a logo for the company and need a web site that clearly represents the fact we are an executive/luxury brand in private hire vehicles. We offer airport transfers, train station transfers, seaport transfers, holiday transfers and business to business pick up and drop off.

Target Market(s)

Corporate people, holidaymakers looking for a luxury start their holiday. VIPs' and celebrities.

Number of Pages Required

5+ page

Font styles to use
Serif
Sans Serif
Decorative
Script

Colors

Designer to choose colors to be used in the design.

Requirements
Must have
• Home Page, Services, About Us, VIP and Contact us
• Please see www.brivomotors.co.uk I have started it but not happy with it at all.
Nice to have
• Booking form or enquiry form.

```html
<!DOCTYPE html>
<html lang="en">
<head>
<meta charset="utf-8">
<title>Halden Travel – Executive Chauffeur Service</title>
<link href="https://fonts.googleapis.com/css2?family=Poppins:wght@400;500;600;700&display=swap" rel="stylesheet">
<style>
:root{
  --orange:#f7941d;
  --orange-dark:#e8830f;
  --ink:#111111;
  --text:#333333;
  --muted:#555555;
  --line:#d9d9d9;
  --dark:#1b1b1b;
  --footer:#0d0d0d;
  --white:#ffffff;
}
*{box-sizing:border-box;margin:0;padding:0}
html,body{width:1200px;height:4167px;overflow:hidden}
body{font-family:'Poppins',sans-serif;color:var(--text);background:var(--white);position:relative}
.abs{position:absolute}

/* header */
.site-header{position:absolute;top:0;left:0;width:1200px;height:111px;background:var(--white)}
.brand{position:absolute;left:144px;top:18px;display:flex;align-items:center;gap:14px}
.brand-dot{width:62px;height:62px;border-radius:50%;background:var(--orange)}
.brand-name{font-size:34px;font-weight:600;color:var(--orange)}
.header-phone{position:absolute;left:755px;top:20px;font-size:24px;font-weight:500;color:var(--ink);display:flex;align-items:center;gap:8px}
.login-btn{position:absolute;left:950px;top:18px;background:var(--orange);color:var(--white);font-size:16px;font-weight:600;padding:6px 20px;border-radius:20px}
.main-nav{position:absolute;right:142px;top:70px;display:flex;gap:36px;font-size:18px;font-weight:500;color:var(--ink);letter-spacing:.5px}

/* hero */
.hero{position:absolute;top:111px;left:0;width:1200px;height:634px;background:linear-gradient(100deg,#3a2a20 0%,#6b5443 35%,#8d7a6a 60%,#4a3b30 100%)}
.booking{position:absolute;left:319px;top:203px;width:564px;height:292px;background:var(--white);padding:18px 26px}
.booking h2{text-align:center;font-size:32px;font-weight:700;color:var(--ink);margin-bottom:14px}
.booking .grid{display:grid;grid-template-columns:1fr 1fr;gap:10px 14px}
.field{height:38px;border:1px solid var(--line);font-size:12px;color:#777;padding:0 12px;display:flex;align-items:center;justify-content:space-between}
.submit{margin-top:14px;height:44px;background:var(--orange);color:var(--white);font-weight:600;font-size:18px;display:flex;align-items:center;justify-content:center}
.dots{position:absolute;left:562px;top:552px;display:flex;gap:10px}
.dots span{width:14px;height:14px;border-radius:50%;background:var(--white)}
.dots span:first-child{border:3px solid var(--white);background:transparent}

/* section titles */
.section-title{position:absolute;left:0;width:1200px;text-align:center;font-size:38px;font-weight:500;color:var(--ink)}
.section-title b{font-weight:700}

/* services */
.service{position:absolute;width:280px;text-align:center}
.service-pin{width:140px;height:150px;margin:0 auto}
.service h3{font-size:19px;font-weight:600;color:var(--ink);margin-top:30px;line-height:1.3}
.service p{font-size:14px;line-height:1.75;color:var(--muted);margin-top:12px}
.arrow{position:absolute;font-size:44px;color:var(--ink);font-weight:300}

/* welcome */
.welcome{position:absolute;top:1361px;left:0;width:1200px;height:583px}
.welcome-content{position:absolute;top:128px;left:0;width:1200px;text-align:center;color:var(--white)}
.welcome-content h2{font-size:40px;font-weight:700;letter-spacing:1px}
.welcome-content p{width:780px;margin:22px auto 0;font-size:19px;line-height:1.95}
.btn-outline{display:inline-block;margin-top:40px;border:2px solid var(--white);border-radius:24px;padding:7px 30px;font-size:16px;font-weight:600;color:var(--white)}

/* app */
.app-heading{position:absolute;left:144px;top:2030px;font-size:34px;font-weight:700;color:var(--ink)}
.app-text{position:absolute;left:144px;top:2096px;width:500px;font-size:16.5px;line-height:2.1;color:var(--text)}
.store{position:absolute;top:2315px;width:140px;height:46px;border-radius:7px;background:var(--ink)}
.phone-visual{position:absolute;left:708px;top:1986px;width:320px;height:528px;border-radius:40px 40px 0 0;background:linear-gradient(160deg,#2b2b2b 0%,#e6e6e6 30%,#d9c6b0 70%,#c7a98c 100%)}

/* testimonials */
.testimonials{position:absolute;top:2514px;left:0;width:1200px;height:394px;background:linear-gradient(90deg,var(--orange-dark),var(--orange) 50%,var(--orange-dark))}
.testimonials h2{position:absolute;top:50px;width:1200px;text-align:center;font-size:38px;font-weight:600;color:var(--white)}
.client-photo{position:absolute;left:219px;top:144px;width:184px;height:184px;border-radius:50%;border:6px solid var(--white);background:linear-gradient(180deg,#d8c6b4,#6d5a4d)}
.quote-mark{position:absolute;font-size:96px;font-weight:700;color:var(--white);line-height:1}
.quote{position:absolute;left:467px;top:150px;width:520px;font-size:16.5px;line-height:1.8;color:var(--white);font-weight:500}
.client-name{position:absolute;left:467px;top:276px;font-size:17px;line-height:1.7;color:var(--white)}
.testimonials .arrow{color:var(--white);top:160px}

/* blog */
.post{position:absolute;top:3081px;width:287px}
.post-image{height:180px;position:relative;background:linear-gradient(135deg,#8b95a2,#c9c2b8 50%,#5a6470)}
.post-date{position:absolute;left:0;bottom:0;width:54px;height:60px;background:var(--orange);color:var(--white);text-align:center;font-weight:700;font-size:22px;line-height:1;padding-top:10px}
.post-date small{display:block;font-size:10px;font-weight:500;margin-top:3px}
.post h3{font-size:17px;font-weight:500;color:var(--ink);margin-top:22px}
.post p{font-size:13px;line-height:1.7;color:var(--muted);margin-top:8px}

/* partners */
.partner{position:absolute;top:3556px;width:175px;height:78px;border:1px solid var(--line);display:flex;align-items:center;justify-content:center}
.partner span{width:110px;height:26px;background:#cfcfcf;border-radius:4px}

/* footer */
.site-footer{position:absolute;top:3728px;left:0;width:1200px;height:439px;background:var(--footer);color:var(--white)}
.footer-badge{position:absolute;left:138px;top:80px;width:96px;height:96px;border-radius:50%;background:var(--white);display:flex;align-items:center;justify-content:center}
.footer-badge span{width:52px;height:52px;border-radius:50%;background:var(--orange)}
.site-footer h4{font-size:19px;font-weight:600;letter-spacing:.5px}
.footer-col{position:absolute;top:56px}
.contact-list{margin-top:30px;font-size:14px;line-height:1.6}
.contact-list li{list-style:none;display:flex;gap:16px;margin-bottom:14px}
.contact-list svg{flex:none;margin-top:3px}
.signup p{font-size:13px;line-height:1.8;margin-top:24px;width:280px;color:#ddd}
.email-field{margin-top:18px;width:275px;height:36px;border-radius:18px;background:var(--white);color:#888;font-size:12px;padding:0 16px;display:flex;align-items:center}
.subscribe-row{display:flex;align-items:center;gap:14px;margin-top:18px}
.subscribe{background:var(--orange);color:var(--ink);font-size:13px;font-weight:700;padding:6px 18px;border-radius:16px}
.social{width:28px;height:28px;border:1.5px solid var(--white);border-radius:50%}
.quick-links{margin-top:26px;list-style:none;font-size:15px;line-height:2}
.footer-rule{position:absolute;left:0;top:342px;width:1200px;height:1px;background:#2a2a2a}
.copyright{position:absolute;top:380px;width:1200px;text-align:center;font-size:14px}
</style>
</head>
<body>

<header class="site-header">
  <div class="brand"><span class="brand-dot"></span><span class="brand-name">Halden Travel</span></div>
  <div class="header-phone">
    <svg width="22" height="22" viewBox="0 0 24 24"><path fill="#111" d="M6.6 10.8a15 15 0 0 0 6.6 6.6l2.2-2.2c.3-.3.7-.4 1-.2 1.1.4 2.3.6 3.6.6.6 0 1 .4 1 1V20c0 .6-.4 1-1 1A17 17 0 0 1 3 4c0-.6.4-1 1-1h3.5c.6 0 1 .4 1 1 0 1.3.2 2.5.6 3.6.1.3 0 .7-.2 1z"/></svg>
    555-010-2048
  </div>
  <div class="login-btn">LOG IN</div>
  <nav class="main-nav"><span>HOME</span><span>SERVICES</span><span>ABOUT US</span><span>VIP</span><span>CONTACT US</span></nav>
</header>

<section class="hero" role="img" aria-label="Businesswoman on the phone in the back seat of a luxury car">
  <form class="booking">
    <h2>BOOK A RIDE WITH US</h2>
    <div class="grid">
      <div class="field">First Name</div><div class="field">Last Name</div>
      <div class="field">Email</div><div class="field">Phone</div>
      <div class="field">Date <svg width="14" height="14" viewBox="0 0 14 14"><rect x="1" y="2" width="12" height="11" fill="none" stroke="#777"/><line x1="1" y1="5" x2="13" y2="5" stroke="#777"/></svg></div><div class="field">Time</div>
    </div>
    <div class="submit">SUBMIT</div>
  </form>
  <div class="dots"><span></span><span></span><span></span><span></span></div>
</section>

<h2 class="section-title" style="top:805px"><b>OUR</b> SERVICES</h2>
<svg class="abs" style="left:300px;top:985px" width="600" height="4"><line x1="0" y1="2" x2="600" y2="2" stroke="#999" stroke-dasharray="5 5"/></svg>
<span class="arrow" style="left:90px;top:1065px">&#8249;</span>
<span class="arrow" style="left:1085px;top:1065px">&#8250;</span>

<div class="service" style="left:132px;top:905px">
  <svg class="service-pin" viewBox="0 0 140 150"><path d="M70 4a62 62 0 0 1 0 124 62 62 0 0 1 0-124z" fill="var(--orange)"/><path d="M30 110 70 148 110 110z" fill="var(--orange)"/><circle cx="70" cy="66" r="40" fill="#fff"/><path d="M48 66h44M70 50l14 16-14 16" stroke="#111" stroke-width="6" fill="none"/></svg>
  <h3>AIRPORT TRANSFERS</h3>
  <p>Airport and Seaport transfers are a particular speciality of ours. We have in depth knowledge of the road network around all major airports and seaports alike. We have the very latest traffic monitoring software.</p>
</div>
<div class="service" style="left:466px;top:905px">
  <svg class="service-pin" viewBox="0 0 140 150"><path d="M70 4a62 62 0 0 1 0 124 62 62 0 0 1 0-124z" fill="var(--orange)"/><path d="M30 110 70 148 110 110z" fill="var(--orange)"/><circle cx="70" cy="66" r="40" fill="#fff"/><rect x="50" y="60" width="40" height="16" rx="4" fill="#111"/><circle cx="58" cy="80" r="5" fill="#111"/><circle cx="82" cy="80" r="5" fill="#111"/></svg>
  <h3>BUSINESS TO BUSINESS TRANSFERS</h3>
  <p>If its a stress free chauffeur service you need then look no further. A selection of vehicles to choose from that all come with full leather and air conditioning. Meaning you turn up to your</p>
</div>
<div class="service" style="left:791px;top:905px">
  <svg class="service-pin" viewBox="0 0 140 150"><path d="M70 4a62 62 0 0 1 0 124 62 62 0 0 1 0-124z" fill="var(--orange)"/><path d="M30 110 70 148 110 110z" fill="var(--orange)"/><circle cx="70" cy="66" r="40" fill="#fff"/><circle cx="70" cy="46" r="6" fill="#111"/><path d="M70 54v20l-10 16M70 74l10 16M58 64h24" stroke="#111" stroke-width="5" fill="none"/></svg>
  <h3>HOLIDAY TRANSFERS</h3>
  <p>Why not start your holiday off stress free and allow us to take care of your outbound and return journey to and from the airport, seaport or train station. Our drivers will take your luggage from your door</p>
</div>

<section class="welcome">
  <svg class="abs" style="left:0;top:0" width="1200" height="583" viewBox="0 0 1200 583">
    <polygon points="0,0 1200,80 1200,583 0,583" fill="var(--dark)" role="img" aria-label="Chauffeur standing beside an executive car"/>
    <polygon points="0,0 640,42 0,100" fill="var(--orange)"/>
    <polygon points="0,0 1200,80 1200,110 300,50" fill="var(--orange)" opacity=".0"/>
    <polygon points="1200,470 1200,545 660,530" fill="var(--orange)"/>
    <polygon points="0,583 1200,545 1200,583" fill="var(--white)"/>
  </svg>
  <div class="welcome-content">
    <h2>WELCOME TO HALDEN TRAVEL</h2>
    <p>Sed ut perspiciatis unde omnis iste natus error sit voluptatem accusantium doloremque laudantium, totam rem aperiam, eaque ipsa quae ab illo inventore veritatis et quasi architecto beatae vitae dicta sunt explicabo. Nemo enim ipsam voluptatem quia voluptas sit aspernatur aut odit aut fugit</p>
    <span class="btn-outline">READ MORE</span>
  </div>
</section>

<h2 class="app-heading">ALWAYS HERE FOR YOU</h2>
<p class="app-text">We provide airport transfers to and from all major UK airports, seaports, train station transfers and an executive business to business transfer service. Whether you have an individual or group transfer request, our company-owned fleet offers a choice of options to suit your needs, from luxury saloons and SUV's to 9-seat luxury transports.</p>
<div class="store" style="left:144px"></div>
<div class="store" style="left:298px"></div>
<div class="phone-visual" role="img" aria-label="Hand holding a smartphone showing a booking map"></div>

<section class="testimonials">
  <h2>CLIENT TESTIMONIALS</h2>
  <span class="arrow" style="left:148px">&#8249;</span>
  <span class="arrow" style="left:1025px">&#8250;</span>
  <div class="client-photo" role="img" aria-label="Portrait of a satisfied client"></div>
  <span class="quote-mark" style="left:405px;top:130px">&ldquo;</span>
  <p class="quote">Aociosqu ad litora torquent per conubia nostra per inceptos hymenaeos Proin nulla arcu nonummy luctus dictum eget fermentum et lorem Nunc porta convallis pede Aociosqu ad litora torquent per conubia nostra per inceptos</p>
  <p class="client-name">Daniel Rourke,<br>Halden Travel</p>
  <span class="quote-mark" style="left:588px;top:300px">&rdquo;</span>
</section>

<h2 class="section-title" style="top:2980px"><b>FROM THE BLOG</b></h2>
<article class="post" style="left:144px">
  <div class="post-image" role="img" aria-label="Travellers with luggage at a station"><div class="post-date">02<small>FEB</small></div></div>
  <h3>Sed ut perspiciatis unde omnis</h3>
  <p>Vestibulum sagittis nisl nec pellentesque suscipit, arcu nisi maximus neque, vitae finibus erat odio eu lacus. Cras malesuada elit nunc.</p>
</article>
<article class="post" style="left:456px">
  <div class="post-image" role="img" aria-label="Business travellers walking through a terminal"><div class="post-date">02<small>FEB</small></div></div>
  <h3>Sed ut perspiciatis unde omnis</h3>
  <p>Vestibulum sagittis nisl nec pellentesque suscipit, arcu nisi maximus neque, vitae finibus erat odio eu lacus. Cras malesuada elit nunc.</p>
</article>
<article class="post" style="left:770px">
  <div class="post-image" role="img" aria-label="Woman with a suitcase beside a red car"><div class="post-date">02<small>FEB</small></div></div>
  <h3>Sed ut perspiciatis unde omnis</h3>
  <p>Vestibulum sagittis nisl nec pellentesque suscipit, arcu nisi maximus neque, vitae finibus erat odio eu lacus. Cras malesuada elit nunc.</p>
</article>

<h2 class="section-title" style="top:3458px"><b>OUR</b> PARTNERS</h2>
<span class="arrow" style="left:84px;top:3555px;color:#bbb">&#8249;</span>
<span class="arrow" style="left:1086px;top:3555px;color:#bbb">&#8250;</span>
<div class="partner" style="left:130px"><span></span></div>
<div class="partner" style="left:319px"><span></span></div>
<div class="partner" style="left:511px"><span></span></div>
<div class="partner" style="left:700px"><span></span></div>
<div class="partner" style="left:889px"><span></span></div>

<footer class="site-footer">
  <div class="footer-badge"><span></span></div>
  <div class="footer-col" style="left:275px">
    <h4>CONTACT US</h4>
    <ul class="contact-list">
      <li><svg width="14" height="18" viewBox="0 0 14 18"><path d="M7 1a6 6 0 0 1 6 6c0 4-6 10-6 10S1 11 1 7a6 6 0 0 1 6-6z" fill="none" stroke="#fff"/><circle cx="7" cy="7" r="2" fill="#fff"/></svg><span>Halden Travel<br>48 Harbour Lane, Unit #2<br>Westfield.</span></li>
      <li><svg width="14" height="14" viewBox="0 0 24 24"><path fill="none" stroke="#fff" stroke-width="2" d="M6.6 10.8a15 15 0 0 0 6.6 6.6l2.2-2.2 5 1.4V20A17 17 0 0 1 3 4h4.5l1.4 5z"/></svg><span>Phone : +555 0134 7781</span></li>
      <li><svg width="16" height="12" viewBox="0 0 16 12"><rect x="1" y="1" width="14" height="10" fill="none" stroke="#fff"/><path d="M1 1l7 6 7-6" fill="none" stroke="#fff"/></svg><span>Email : info@haldentravel.co.uk</span></li>
    </ul>
  </div>
  <div class="footer-col signup" style="left:586px">
    <h4>SIGN UP TO RECEIVE EMAIL</h4>
    <p>Excepteur sint occaecat cupidatat non proident, sunt in culpa qui Nemo enim ipsam</p>
    <div class="email-field">Enter Email</div>
    <div class="subscribe-row"><span class="subscribe">SUBSCRIBE</span><span class="social"></span><span class="social"></span><span class="social"></span><span class="social"></span></div>
  </div>
  <div class="footer-col" style="left:928px">
    <h4>QUICK LINKS</h4>
    <ul class="quick-links"><li>Home</li><li>Services</li><li>About Us</li><li>VIP</li><li>Contact us</li></ul>
  </div>
  <div class="footer-rule"></div>
  <p class="copyright">Copyright © Halden Travel. 2018. All rights reserved.</p>
</footer>

</body>
</html>
```